Redesign Our Presentation on Rational Prescribing

We are looking for a new designer for KVMed, a project that creates educational modules for healthcare providers in the District of Columbia (more information at healthbureau-example.org/kvmed). We want someone to redesign our powerpoints to look clean and professional, with original graphics that reflect the content on the slides. We also want someone who is creative and could potentially also redesign factsheets, written reports, and promotional postcards.

All the text on the slides must stay the same and it must be in the template (red line at the top, with the red box at the bottom, with the Halvern Bureau of Health logo). We want a powerpoint that features original graphics, looks professional, looks clean and is easy to read.

```html
<!DOCTYPE html>
<html lang="en">
<head>
<meta charset="utf-8">
<title>Medication Use in Elders – Halvern Bureau of Health</title>
<link href="https://fonts.googleapis.com/css2?family=Lato:ital,wght@0,300;0,400;0,700;0,900;1,400&display=swap" rel="stylesheet">
<style>
:root{
  --red:#e8202a;
  --navy:#27285f;
  --purple:#4b4a8e;
  --gold:#c3963b;
  --tan:#dccca6;
  --ink:#444;
  --dark:#3b3b3b;
  --ring:#d6d6d6;
  --bg:#e8e8e8;
}
*{margin:0;padding:0;box-sizing:border-box}
html,body{width:1200px;height:1000px;overflow:hidden}
body{background:var(--bg);font-family:'Lato',sans-serif;position:relative;color:var(--ink)}
.slide{position:absolute;width:521px;height:293px;background:#fff;overflow:hidden;box-shadow:0 1px 3px rgba(0,0,0,.12)}
.s1{left:53px;top:182px}.s2{left:626px;top:182px}.s3{left:53px;top:525px}.s4{left:626px;top:525px}
.abs{position:absolute}
.slide-title{position:absolute;left:40px;top:23px;font-size:16px;font-weight:300;color:#333;white-space:nowrap}
.title-rule{position:absolute;left:40px;right:0;top:44px;height:1.5px;background:var(--red)}
.page-no{position:absolute;right:6px;top:6px;width:16px;height:16px;border-radius:3px;background:var(--navy);color:#fff;font-size:8px;display:flex;align-items:center;justify-content:center}
.footer-band{position:absolute;left:0;right:0;bottom:0;height:16px;background:var(--red);color:#fff;font-size:7px;padding-left:16px;line-height:16px}
.brand{position:absolute;left:16px;bottom:22px;display:flex;align-items:center;gap:4px;font-size:7px;font-weight:900;color:var(--navy);line-height:1.05;width:90px}
.brand .dot{width:9px;height:9px;border-radius:50%;background:var(--navy);flex:none}
/* cover */
.cover-bar{left:0;top:0;width:27px;height:100%;background:var(--red)}
.cover-frame{left:133px;top:118px;width:120px;height:112px;border:12px solid var(--tan);border-right:none;border-top:none}
.cover-photo{left:214px;top:20px;width:286px;height:253px;background:linear-gradient(135deg,#eef0f2,#d9dcdf 45%,#e8c3c9 60%,#cfd2d6)}
.cover-title{left:27px;top:42px;width:243px;height:74px;background:var(--purple);border-radius:0 28px 0 0;color:#fff;font-size:27px;font-weight:400;line-height:29px;padding:7px 0 0 13px}
.s1 .brand{left:160px;bottom:90px}
/* multiple medication */
.lead{left:20px;top:95px;width:182px;text-align:right;font-size:12.5px;font-weight:300;line-height:13.4px;color:#333;white-space:nowrap}
.dots{left:209px;top:92px;height:136px;border-left:3px dotted var(--gold)}
.stat{position:absolute;left:225px;display:flex;align-items:baseline;gap:6px}
.stat b{font-size:29px;font-weight:900;letter-spacing:-.5px}
.stat span{font-size:8.5px;color:#555}
.stat em{font-style:normal;font-weight:900}
.c-gold{color:var(--gold)}.c-navy{color:var(--navy)}.c-red{color:var(--red)}
.cite{right:25px;top:215px;font-size:9px;font-style:italic;color:#555}
/* predicting */
.chev{position:absolute;width:22px;height:34px}
.point{position:absolute;left:95px;font-size:10px;line-height:11.5px;color:#555;width:210px}
.point i{font-style:normal;color:var(--red)}
.example{position:absolute;left:319px;width:179px;background:var(--dark);color:#cfcfcf;padding:4px 6px;font-size:7px;line-height:8.7px;text-align:justify;border-radius:0 0 14px 0;overflow:hidden}
.example h4{font-size:8.5px;font-weight:700;margin-bottom:1px}
/* drug classes */
.sub{left:55px;top:57px;display:flex;align-items:center;gap:7px;font-size:9px;color:#555}
.pill-band{left:0;top:85px;width:521px;height:117px;background:linear-gradient(90deg,#f4ecec,#eadada 40%,#f1e6e4 70%,#ecdcd9)}
.donut{position:absolute;top:100px;width:88px;text-align:center}
.donut svg{display:block;margin:0 auto}
.donut .pct{position:absolute;left:0;right:0;top:30px;font-size:19px;font-weight:700}
.donut p{font-size:7.5px;color:#444;margin-top:6px}
.note{left:58px;top:220px;width:440px;font-size:7.3px;line-height:10px;color:#555;white-space:nowrap}
</style>
</head>
<body>

<section class="slide s1">
  <div class="abs cover-bar"></div>
  <div class="abs cover-frame"></div>
  <div class="abs cover-photo" role="img" aria-label="Photo of a young carer helping an older woman sort her medication at a table"></div>
  <h1 class="abs cover-title">Medication<br>Use in Elders.</h1>
  <div class="brand"><span class="dot"></span>Halvern Bureau of Health</div>
</section>

<section class="slide s2">
  <h2 class="slide-title">Consequences of Multiple Medication Use.</h2>
  <div class="title-rule"></div>
  <div class="page-no">2</div>
  <p class="abs lead">The use of several medications<br>simultaneously, even at<br>otherwise appropriate doses,<br>increases the risk of adverse<br>effects, drug interactions,<br>non-adherence, and death.</p>
  <div class="abs dots"></div>
  <div class="stat" style="top:92px"><b class="c-gold">13%</b><span>The risk of ADRs when taking <em class="c-gold">TWO</em> medicines.</span></div>
  <div class="stat" style="top:136px"><b class="c-navy">58%</b><span>The risk of ADRs when taking <em class="c-navy">FIVE</em> medicines.</span></div>
  <div class="stat" style="top:180px"><b class="c-red">82%</b><span>The risk of ADRs when taking <em class="c-red">SEVEN</em> medicines.</span></div>
  <p class="abs cite">(Marlow 2015)</p>
  <div class="brand"><span class="dot"></span>Halvern Bureau of Health</div>
  <div class="footer-band">www.healthbureau-example.org</div>
</section>

<section class="slide s3">
  <h2 class="slide-title">Predicting ADRs.</h2>
  <div class="title-rule"></div>
  <div class="page-no">3</div>
  <svg class="chev" style="left:66px;top:75px" viewBox="0 0 22 34"><path d="M3 3 L17 17 L3 31" fill="none" stroke="var(--purple)" stroke-width="6" stroke-linejoin="round"/></svg>
  <p class="point" style="top:80px"><i>•</i> Few ADRs represent improper prescribing.<br><i>•</i> Most ADRs are related to the<br>pharmacologic properties of a drug.</p>
  <svg class="chev" style="left:66px;top:158px" viewBox="0 0 22 34"><path d="M3 3 L17 17 L3 31" fill="none" stroke="var(--purple)" stroke-width="6" stroke-linejoin="round"/></svg>
  <p class="point" style="top:166px"><i>•</i> Many ADRs are both predictable and<br>avoidable (Renner &amp; Holt 2015).</p>
  <div class="example" style="top:69px;height:84px">
    <h4 class="c-red">For example:</h4>
    Benzodiazepines cause increased imbalance and gait instability associated with increased risk of falls. A patient taking a nightly benzodiazepine to induce sleep is at high risk for falls. All subsequent health-care costs and associated debility are due to the prescribed medication.
  </div>
  <div class="example" style="top:158px;height:114px">
    <h4 class="c-gold">For example:</h4>
    Anticholinergic medications prescribed to control bladder spasm may result in constipation and even mental status changes. These are expected outcomes from modulating acetylcholine levels. This type of drug-associated adverse effect raises the risk of prescribing additional medications, such as constipation-relieving agents, to address adverse effects of the original drug. Eliminating, changing, or lowering the dose of the original drug is the right course of action.
  </div>
  <div class="brand"><span class="dot"></span>Halvern Bureau of Health</div>
  <div class="footer-band">www.healthbureau-example.org</div>
</section>

<section class="slide s4">
  <h2 class="slide-title">Drug Classes Most Commonly Involved in ADRs</h2>
  <div class="title-rule"></div>
  <div class="page-no">3</div>
  <div class="abs sub"><svg width="9" height="14" viewBox="0 0 9 14"><path d="M2 2 L7 7 L2 12" fill="none" stroke="var(--purple)" stroke-width="2.5"/></svg>ADRs during hospitalization</div>
  <div class="abs pill-band" role="img" aria-label="Soft-focus photo of scattered coloured pills and capsules"></div>
  <div class="donut" style="left:73px">
    <svg width="82" height="82" viewBox="0 0 82 82"><circle cx="41" cy="41" r="35" fill="#fff" stroke="var(--ring)" stroke-width="9"/><circle cx="41" cy="41" r="35" fill="none" stroke="var(--gold)" stroke-width="9" stroke-dasharray="74.8 145" transform="rotate(-90 41 41)"/></svg>
    <span class="pct c-gold">34%</span><p>Cardiovascular agents</p>
  </div>
  <div class="donut" style="left:216px">
    <svg width="82" height="82" viewBox="0 0 82 82"><circle cx="41" cy="41" r="35" fill="#fff" stroke="var(--ring)" stroke-width="9"/><circle cx="41" cy="41" r="35" fill="none" stroke="var(--navy)" stroke-width="9" stroke-dasharray="39.6 180" transform="rotate(-90 41 41)"/></svg>
    <span class="pct c-navy">18%</span><p>Analgesic medications</p>
  </div>
  <div class="donut" style="left:352px">
    <svg width="82" height="82" viewBox="0 0 82 82"><circle cx="41" cy="41" r="35" fill="#fff" stroke="var(--ring)" stroke-width="9"/><circle cx="41" cy="41" r="35" fill="none" stroke="var(--red)" stroke-width="9" stroke-dasharray="22 200" transform="rotate(-90 41 41)"/></svg>
    <span class="pct c-red">10%</span><p>Anti-diabetic drugs</p>
  </div>
  <p class="abs note">Predictors of ADRs included the number of medications, use of hypoglycaemic agents, history of hyperlipidaemia,<br>raised white cell count on admission and length of stay. (Okafor-Lind 2012)</p>
  <div class="brand"><span class="dot"></span>Halvern Bureau of Health</div>
  <div class="footer-band">www.healthbureau-example.org</div>
</section>

</body>
</html>
```